KLV Plant Services

We are a heavy diesel mechanical business with additional air con certificates, remapping engine rebuilt

Contact Information for Business Card

Company Name, Director Name, Managing Director, Contact details, email and website

Font styles to use
Serif
Script

```html
<!DOCTYPE html>
<html lang="en">
<head>
<meta charset="utf-8">
<title>KLV Plant Services – Business Card</title>
<link href="https://fonts.googleapis.com/css2?family=Montserrat:wght@400;500;700&display=swap" rel="stylesheet">
<style>
  :root {
    --backdrop: #d0d0d0;
    --card: #ffffff;
    --navy: #16127d;
    --ink: #0b0b0b;
    --text: #1c1c1c;
    --rule: #9a9a9a;
  }
  * { margin: 0; padding: 0; box-sizing: border-box; }
  html, body { width: 1146px; height: 1200px; overflow: hidden; }
  body {
    background: var(--backdrop);
    font-family: "Montserrat", sans-serif;
    color: var(--text);
    position: relative;
  }
  .card {
    position: absolute;
    left: 233px;
    width: 697px;
    height: 401px;
    background: var(--card);
    overflow: hidden;
  }
  .card--front { top: 145px; }
  .card--back {
    top: 619px;
    display: flex;
    align-items: center;
    justify-content: center;
  }

  .company-name {
    color: var(--navy);
    font-weight: 700;
    line-height: 1;
    white-space: nowrap;
  }
  .card--front .company-name {
    position: absolute;
    left: 30px;
    width: 260px;
    top: 184px;
    text-align: center;
    font-size: 23px;
  }
  .card--back .company-name { font-size: 40px; margin-top: -30px; }

  .divider {
    position: absolute;
    left: 307px; top: 93px;
    width: 1px; height: 220px;
    background: var(--rule);
  }
  .details { position: absolute; left: 330px; top: 84px; }
  .details__name {
    font-size: 37px; font-weight: 700; color: var(--navy);
    letter-spacing: 0.3px; line-height: 1.1;
  }
  .details__role {
    font-size: 17px; font-weight: 500; color: var(--ink);
    margin-top: 2px; letter-spacing: 0.3px;
  }
  .contact-list { list-style: none; margin-top: 16px; }
  .contact-list li {
    display: flex; align-items: center; gap: 9px;
    font-size: 19px; height: 28px;
  }
  .contact-list svg { width: 18px; height: 18px; flex: none; fill: var(--navy); }
  .address { margin-top: 14px; font-size: 19px; line-height: 27px; }

  .band { position: absolute; left: 0; bottom: 0; width: 697px; height: 16px; }
</style>
</head>
<body>
  <section class="card card--front">
    <p class="company-name">KLV Plant Services</p>
    <div class="divider"></div>
    <div class="details">
      <h1 class="details__name">DANIEL CARTER</h1>
      <p class="details__role">MANAGING DIRECTOR</p>
      <ul class="contact-list">
        <li>
          <svg viewBox="0 0 24 24" aria-hidden="true"><path d="M6.6 10.8a15.1 15.1 0 0 0 6.6 6.6l2.2-2.2a1 1 0 0 1 1-.25 11.4 11.4 0 0 0 3.6.57 1 1 0 0 1 1 1V20a1 1 0 0 1-1 1A17 17 0 0 1 3 4a1 1 0 0 1 1-1h3.5a1 1 0 0 1 1 1c0 1.25.2 2.45.57 3.57a1 1 0 0 1-.25 1z"/></svg>
          044-987 654 321
        </li>
        <li>
          <svg viewBox="0 0 24 24" aria-hidden="true"><path d="M2 5h20v14H2zm2 2v.5l8 5 8-5V7l-8 5z"/></svg>
          info@klvplantservices.com
        </li>
        <li>
          <svg viewBox="0 0 24 24" aria-hidden="true"><path d="M12 2a10 10 0 1 0 0 20 10 10 0 0 0 0-20zm6.9 6h-2.9a15 15 0 0 0-1.4-3.6A8 8 0 0 1 18.9 8zM12 4c.8 1.2 1.5 2.5 1.9 4h-3.8c.4-1.5 1.1-2.8 1.9-4zM4.3 14a8 8 0 0 1 0-4h3.4a16 16 0 0 0 0 4zm.8 2h2.9c.3 1.3.8 2.5 1.4 3.6A8 8 0 0 1 5.1 16zM8 8H5.1a8 8 0 0 1 4.3-3.6C8.8 5.5 8.4 6.7 8 8zm4 12c-.8-1.2-1.5-2.5-1.9-4h3.8c-.4 1.5-1.1 2.8-1.9 4zm2.3-6H9.7a14 14 0 0 1 0-4h4.6a14 14 0 0 1 0 4zm.3 5.6c.6-1.1 1.1-2.3 1.4-3.6h2.9a8 8 0 0 1-4.3 3.6zM16.3 14a16 16 0 0 0 0-4h3.4a8 8 0 0 1 0 4z"/></svg>
          www.klvplantservices.com
        </li>
      </ul>
      <p class="address">421, Address line goes here<br>45452, Country name</p>
    </div>
    <svg class="band" viewBox="0 0 697 16" preserveAspectRatio="none" aria-hidden="true">
      <polygon points="0,0 358,0 330,16 0,16" fill="var(--ink)"/>
      <polygon points="372,0 697,0 697,16 344,16" fill="var(--navy)"/>
    </svg>
  </section>

  <section class="card card--back">
    <p class="company-name">KLV Plant Services</p>
  </section>
</body>
</html>
```